Building Design company needing a letterhead

We need a letter head for our Building Design company to send letters etc. to our clients, consultants, councils etc. We would like to see our logo used and company colours. I have attached our style guide and an example of our current letterheads. Top left we would like our logo, top right we would like the company details and at the footer we would like some sort of image/design etc. that suits our brand. I like the Tarrow Design letterhead attached.

Target Market(s)

Professionals, Councils, Consultants, Mums & Dads

Industry/Entity Type

Architecture

Other font styles liked:
• refer the design style guide

Colors
f37122
000000
1b1b1b

Requirements
Must have
• Must have the minimum of a logo, company details and footer
Nice to have
• An image/design made for the footer that would suite our brand and website at www.corvanplans.com.au. Also it would be nice to include the KMEOT logo somewhere perhaps included in the footer.
Should not have
• Large images in the header. I just want the logo and company details.

```html
<!DOCTYPE html>
<html lang="en">
<head>
<meta charset="utf-8">
<title>Corvan Plans Letterhead</title>
<link rel="stylesheet" href="https://fonts.googleapis.com/css2?family=Fira+Sans:wght@300;800&family=Open+Sans:wght@400;600&display=swap">
<style>
  :root {
    --backdrop: #5c4b42;
    --paper: #ffffff;
    --brand-orange: #e65a25;
    --ink: #1b1b1b;
    --band-dark: #333333;
    --band-grey: #9a9a9c;
    --footer-text: #ffffff;
  }
  html, body {
    margin: 0;
    padding: 0;
    width: 967px;
    height: 1200px;
    overflow: hidden;
    background: var(--backdrop);
  }
  .sheet {
    position: absolute;
    left: 135px;
    top: 133px;
    width: 720px;
    height: 932px;
    background: var(--paper);
    box-shadow: 3px 4px 6px rgba(0,0,0,0.45);
    overflow: hidden;
    font-family: "Open Sans", sans-serif;
  }
  .brand {
    position: absolute;
    left: 52px;
    top: 38px;
    display: flex;
    align-items: center;
    gap: 22px;
  }
  .brand-square {
    width: 66px;
    height: 66px;
    background: var(--brand-orange);
  }
  .brand-name {
    font-family: "Fira Sans", sans-serif;
    color: var(--ink);
    line-height: 1;
  }
  .brand-name .line-bold {
    display: block;
    font-weight: 800;
    font-size: 40px;
    letter-spacing: 1.5px;
  }
  .brand-name .line-light {
    display: block;
    font-weight: 800;
    font-size: 40px;
    letter-spacing: 1.5px;
    margin-top: 4px;
  }
  .partner {
    position: absolute;
    left: 584px;
    top: 38px;
    width: 64px;
    text-align: center;
  }
  .partner-square {
    width: 56px;
    height: 56px;
    margin: 0 auto;
    border: 3px solid var(--brand-orange);
    box-sizing: border-box;
  }
  .partner-name {
    margin-top: 8px;
    font-family: "Open Sans", sans-serif;
    font-size: 14px;
    color: var(--brand-orange);
    letter-spacing: 0.5px;
  }
  .footer-waves {
    position: absolute;
    left: 0;
    top: 824px;
    width: 720px;
    height: 108px;
    display: block;
  }
  .footer-details {
    position: absolute;
    left: 0;
    top: 0;
    width: 720px;
    height: 932px;
    pointer-events: none;
    color: var(--footer-text);
    font-size: 11px;
    line-height: 16.5px;
  }
  .detail-address { position: absolute; left: 40px; top: 885px; }
  .detail-contact { position: absolute; left: 317px; top: 885px; }
  .detail-web { position: absolute; right: 39px; top: 883px; text-align: right; }
  .detail-web .site {
    display: block;
    font-weight: 600;
    font-size: 13.5px;
    letter-spacing: 0.3px;
    margin-top: 1px;
  }
  .divider {
    position: absolute;
    top: 888px;
    width: 1px;
    height: 26px;
    background: rgba(160, 50, 20, 0.6);
  }
  .divider.first { left: 284px; }
  .divider.second { left: 454px; }
</style>
</head>
<body>
  <div class="sheet">
    <header>
      <div class="brand">
        <div class="brand-square"></div>
        <div class="brand-name">
          <span class="line-bold">CORVAN</span>
          <span class="line-light">PLANS</span>
        </div>
      </div>
      <div class="partner">
        <div class="partner-square"></div>
        <div class="partner-name">KMEOT</div>
      </div>
    </header>

    <svg class="footer-waves" viewBox="0 1030 900 135" preserveAspectRatio="none" aria-hidden="true">
      <path d="M0 1080 C80 1060 160 1050 235 1047 C160 1052 80 1065 0 1088 Z" fill="var(--band-grey)"/>
      <path d="M520 1068 C640 1082 780 1080 900 1050 L900 1056 C780 1088 640 1088 520 1068 Z" fill="var(--band-grey)"/>
      <path d="M0 1090 C120 1058 220 1050 300 1052 C400 1054 470 1075 600 1088 C720 1098 820 1084 900 1066 L900 1070 C820 1090 720 1102 600 1093 C470 1082 400 1058 300 1057 C220 1056 120 1064 0 1094 Z" fill="var(--band-dark)"/>
      <path d="M0 1097 C120 1070 220 1062 300 1063 C400 1065 470 1085 600 1097 C720 1106 820 1093 900 1071 L900 1165 L0 1165 Z" fill="var(--brand-orange)"/>
    </svg>

    <footer class="footer-details">
      <div class="detail-address">
        Unit 3/22 Harlow Way Westbrook WA 6999<br>
        PO Box 5870 Westbrook North WA 6999
      </div>
      <div class="divider first"></div>
      <div class="detail-contact">
        Ph: (08) 5550 1842<br>
        ABN 00 123 456 789
      </div>
      <div class="divider second"></div>
      <div class="detail-web">
        email: admin@corvanplans.com.au
        <span class="site">www.corvanplans.com.au</span>
      </div>
    </footer>
  </div>
</body>
</html>
```